Varnex Consulting Business card design.

See our website www.varnexconsulting.example which will give you a good idea of what we are about. The font is called 'Play'.

I'd like a standout business card in keeping with the themes and branding on the website

Target Market(s)

professionals. HR directors

Industry/Entity Type

Business

Contact Information for Business Card

Varnex Consulting PO Box 3172 Merrowdale NSW 2291 1300 485 193 Gavin Threlkeld Principal email: career@varnexconsulting.example ABN: 71203948865

Font styles to use
Other font styles liked:
• Play

Requirements
Must have
• Must have same design colours and branding as website.
• On back I'd prefer a list of the things we do which appears below the name at the header on the website

```html
<!DOCTYPE html>
<html lang="en">
<head>
<meta charset="utf-8">
<title>Varnex Consulting – Business Card</title>
<link href="https://fonts.googleapis.com/css2?family=Play:wght@400;700&display=swap" rel="stylesheet">
<style>
  :root {
    --backdrop: #3a3a3a;
    --navy: #0b1f33;
    --frame-light: #e4e6e8;
    --frame-blue: #1f8ad9;
    --accent: #2189d6;
    --text-light: #e8ecef;
    --divider: #c9d2da;
    --photo-top: #b9bcbe;
    --photo-mid: #d4d6d7;
    --photo-low: #6f8582;
  }
  * { margin: 0; padding: 0; box-sizing: border-box; }
  html, body {
    width: 1200px; height: 750px; overflow: hidden;
    background: var(--backdrop);
    font-family: 'Play', sans-serif;
  }
  .card {
    position: absolute; top: 215px;
    width: 499px; height: 285px;
    background: linear-gradient(to bottom, var(--frame-light) 0 146px, var(--frame-blue) 146px 100%);
  }
  .card--front { left: 88px; }
  .card--back { left: 617px; }
  .card__panel {
    position: absolute; left: 6px; top: 6px; right: 8px; bottom: 8px;
    background: var(--navy);
  }
  .line {
    position: absolute; left: 0; width: 100%;
    text-align: center; white-space: nowrap;
  }
  .wordmark { font-size: 32px; line-height: 32px; letter-spacing: 0.5px; color: var(--text-light); }
  .wordmark__accent { color: var(--accent); }
  .services { font-size: 9.5px; line-height: 10px; letter-spacing: 1.1px; color: var(--accent); }
  .services .sep { color: var(--text-light); margin: 0 4px; }
  .divider {
    position: absolute; left: 34px; right: 34px; top: 108px;
    height: 1px; background: var(--divider);
  }
  .person-name { font-size: 21px; line-height: 22px; color: var(--accent); letter-spacing: 0.3px; }
  .person-role { font-size: 17px; line-height: 18px; color: var(--text-light); }
  .abn { font-size: 14.5px; line-height: 16px; color: var(--text-light); }
  .contact { font-size: 13px; line-height: 14px; color: var(--text-light); }
  .photo {
    position: absolute; left: 0; top: 0; right: 0; height: 207px;
    background: linear-gradient(to bottom, var(--photo-top) 0%, var(--photo-mid) 60%, var(--photo-low) 100%);
  }
  .card--back .wordmark { font-size: 29px; line-height: 30px; }
  .card--back .services { font-size: 9px; }
</style>
</head>
<body>

<div class="card card--front">
  <div class="card__panel">
    <div class="line wordmark" style="top:31px;">VARNEX <span class="wordmark__accent">CONSULTING</span></div>
    <div class="line services" style="top:78px;">Search &amp; Select<span class="sep">I</span>Career<span class="sep">I</span>Coaching<span class="sep">I</span>Leadership<span class="sep">I</span>Outplacement</div>
    <div class="divider"></div>
    <div class="line person-name" style="top:127px;">Gavin Threlkeld</div>
    <div class="line person-role" style="top:148px;">Principal</div>
    <div class="line abn" style="top:182px;">ABN: 71203948865</div>
    <div class="line contact" style="top:213px;">1300 485 193</div>
    <div class="line contact" style="top:230px;">career@varnexconsulting.example</div>
    <div class="line contact" style="top:249px;">PO Box 3172 Merrowdale NSW 2291</div>
  </div>
</div>

<div class="card card--back">
  <div class="card__panel">
    <div class="photo" role="img" aria-label="Photo of a surfer in a wetsuit riding a white board through breaking spray"></div>
    <div class="line wordmark" style="top:213px;">VARNEX <span class="wordmark__accent">CONSULTING</span></div>
    <div class="line services" style="top:255px;">Search &amp; Select<span class="sep">I</span>Career<span class="sep">I</span>Coaching<span class="sep">I</span>Leadership<span class="sep">I</span>Outplacement</div>
  </div>
</div>

</body>
</html>
```